Forensic Document Examiner, looking for contemporary update to my stationery design.

Looking for professional, classy logo design for stationery and business cards. My current stationery and business card is attached.I believe a logo image makes a header section interesting, so an intriguing design of a pen, feathered pen, microscope, magnifying glass, etc., would be appropriate. I have been in the business for over 30 years. I leave ideas to the imagination of the designer.My work involves mainly, the comparison of signatures and handwriting. I also resolve alterations, obliterations, and work as shown on my website: www.documentexaminer.infoThe image produced will be printed on quality white stationery and envelopes. The stationery will be photocopied by my clients, so the images should be reproducible. The business cards may be designed in other than white.

Target Market(s)

Attorneys

Font styles to use
Sans Serif

Colors

Designer to choose colors to be used in the design.

Requirements
Must have
• Image suitable for white stationery and photocopying.
• Classy logo and image; no casual fonts.
Nice to have
• Intriguing, contemporary design incorporating a relevant logo to my work.

```html
<!DOCTYPE html>
<html lang="en">
<head>
<meta charset="utf-8">
<title>Daniel R. Hale — Business Cards</title>
<link rel="stylesheet" href="https://fonts.googleapis.com/css2?family=Noto+Serif:ital,wght@0,400;0,700;1,400&display=swap">
<style>
  :root {
    --bg: #1b2140;
    --purple: #3b3a86;
    --purple-light: #4a4a9a;
    --purple-dark: #2e2d6e;
    --grey: #c9c9cc;
    --grey-light: #e6e6e8;
    --white: #ffffff;
    --text-grey: #7d7d86;
    --accent: #f3d23a;
  }
  * { box-sizing: border-box; margin: 0; padding: 0; }
  html, body { width: 1200px; height: 900px; overflow: hidden; }
  body {
    background: var(--bg);
    font-family: "Noto Serif", Georgia, serif;
    position: relative;
  }
  .card {
    position: absolute;
    width: 560px;
    height: 320px;
    border-radius: 26px;
    overflow: hidden;
    box-shadow: 0 18px 40px rgba(0,0,0,.45);
  }
  .card-front {
    left: 320px; top: 95px;
    background: linear-gradient(160deg, var(--purple-light), var(--purple-dark));
  }
  .card-back {
    left: 320px; top: 485px;
    background: var(--white);
  }

  /* shared band pieces */
  .band-solid { background: linear-gradient(var(--grey-light), var(--grey)); position: absolute; }
  .band-hatch {
    position: absolute;
    background: repeating-linear-gradient(45deg, var(--grey-light) 0 2px, #f7f7f8 2px 5px);
  }

  /* front */
  .card-front .band-left  { left: 0; top: 200px; width: 150px; height: 24px; }
  .card-front .band-hatch { left: 150px; top: 206px; width: 260px; height: 12px; }
  .card-front .band-right { left: 410px; top: 200px; width: 150px; height: 24px; }
  .mark-circle {
    position: absolute;
    border-radius: 50%;
    background: var(--grey-light);
  }
  .card-front .mark-circle { left: 100px; top: 68px; width: 88px; height: 88px; }
  .card-front .identity { position: absolute; left: 214px; top: 80px; color: var(--white); }
  .name { font-weight: 700; line-height: 1.1; }
  .card-front .name { font-size: 32px; }
  .title { font-weight: 400; color: var(--grey-light); }
  .card-front .title { font-size: 15px; margin-top: 6px; }
  .card-front .website {
    position: absolute; left: 0; right: 0; top: 250px;
    text-align: center; color: var(--white); font-weight: 700; font-size: 17px;
  }

  /* back */
  .brand-panel {
    position: absolute; left: 0; top: 0; width: 232px; height: 320px;
    background: linear-gradient(160deg, var(--purple-light), var(--purple-dark));
    color: var(--white);
  }
  .card-back .mark-circle { left: 76px; top: 52px; width: 80px; height: 80px; }
  .card-back .identity { position: absolute; left: 22px; top: 160px; right: 12px; }
  .card-back .name { font-size: 25px; }
  .card-back .title { font-size: 13px; margin-top: 6px; }
  .card-back .band-top    { left: 232px; top: 0; width: 20px; height: 70px; }
  .card-back .band-hatch  { left: 236px; top: 70px; width: 12px; height: 180px; }
  .card-back .band-bottom { left: 232px; top: 250px; width: 20px; height: 70px; }

  .contact-list {
    position: absolute; left: 276px; top: 28px; list-style: none;
    font-size: 14px; color: var(--text-grey);
  }
  .contact-list li { display: flex; align-items: center; gap: 10px; height: 27px; }
  .contact-list .address { color: var(--purple); }
  .icon { width: 14px; height: 14px; flex: none; }
  .summary {
    position: absolute; left: 276px; top: 160px; width: 262px;
    font-size: 14px; font-weight: 700; color: var(--purple); line-height: 1.5;
  }
</style>
</head>
<body>

<section class="card card-front" aria-label="Business card front">
  <div class="mark-circle" aria-hidden="true"></div>
  <div class="identity">
    <div class="name">Daniel R. Hale</div>
    <div class="title">Forensic Document Examinar</div>
  </div>
  <div class="band-solid band-left"></div>
  <div class="band-hatch"></div>
  <div class="band-solid band-right"></div>
  <div class="website">www.quillmarkreview.info</div>
</section>

<section class="card card-back" aria-label="Business card back">
  <div class="brand-panel">
    <div class="mark-circle" aria-hidden="true"></div>
    <div class="identity">
      <div class="name">Daniel R. Hale</div>
      <div class="title">Forensic Document Examinar</div>
    </div>
  </div>
  <div class="band-solid band-top"></div>
  <div class="band-hatch"></div>
  <div class="band-solid band-bottom"></div>

  <ul class="contact-list">
    <li class="address">
      <svg class="icon" viewBox="0 0 14 14" aria-hidden="true"><circle cx="7" cy="7" r="7" fill="var(--accent)"/><path d="M7 3a2.4 2.4 0 0 0-2.4 2.4C4.6 7.2 7 10.5 7 10.5s2.4-3.3 2.4-5.1A2.4 2.4 0 0 0 7 3z" fill="#fff"/></svg>
      PO Box 4821 Riverton, OR 97520
    </li>
    <li>
      <svg class="icon" viewBox="0 0 14 14" aria-hidden="true"><circle cx="7" cy="7" r="7" fill="var(--accent)"/><path d="M4.5 3.5h1.6l.7 1.8-1 .7a5 5 0 0 0 2.2 2.2l.7-1 1.8.7v1.6c-3.3.3-6.3-2.7-6-6z" fill="#fff"/></svg>
      888-555-0147
    </li>
    <li>
      <svg class="icon" viewBox="0 0 14 14" aria-hidden="true"><circle cx="7" cy="7" r="7" fill="var(--accent)"/><rect x="3.5" y="4.5" width="7" height="5" fill="#fff"/><path d="M3.5 4.5 7 7.3l3.5-2.8" fill="none" stroke="var(--accent)" stroke-width=".8"/></svg>
      dhale@quillmarkreview.info
    </li>
    <li>
      <svg class="icon" viewBox="0 0 14 14" aria-hidden="true"><circle cx="7" cy="7" r="7" fill="var(--accent)"/><circle cx="7" cy="7" r="3.4" fill="none" stroke="#fff" stroke-width=".9"/><path d="M3.6 7h6.8M7 3.6c-1.6 2-1.6 4.8 0 6.8M7 3.6c1.6 2 1.6 4.8 0 6.8" fill="none" stroke="#fff" stroke-width=".7"/></svg>
      www.quillmarkreview.info
    </li>
  </ul>

  <p class="summary">Full service laboratory specializing in handwriting comparisons, obliterations, alterations, indented writing recovery etc.</p>
</section>

</body>
</html>
```